'Little Lantern' promotional brochure

We have designed a 6 week program to educate impending first-time parents about the things they need to know to survive the first 6 months. Sessions delivered by general practitioner/family doctor, dietician, physiotherapist, speech pathologist and psychologist. Our promotional blurb is: 'A comprehensive education program for first-time parents-to-be, delivered over 6 weeks by health professionals in your community, about everything you need to know to look after your baby (and yourself!) in the first 6 months'. I now want to put together a promotional brochure to be distributed to those couples who express an interest which will provide further details of what will be delivered in the course.
Updates
In terms of layout, I envisaged a double sided A4 size, foldable into 3 sections, but very happy to be guided on this.
Target Market(s)
To appeal to a young, well educated demographic. First time parents couples.
Industry/Entity Type
Medical
Font styles to use
Other font styles liked:
- Playfair Display
Requirements
Must have
- Playfair display font to be consistent with our logo (attached). Logo also included please. Some consistency with colours of logo please.
Nice to have
- I am a doctor, and have no creative genes! But prefer a clean and professional appearance overall. Not too cluttered in overall appearance.
Should not have
- No cheesy pictures of babies.

```html
<!DOCTYPE html>
<html lang="en">
<head>
<meta charset="utf-8">
<title>Little Lantern – Brochure</title>
<link rel="stylesheet" href="https://fonts.googleapis.com/css2?family=Playfair+Display:wght@700;900&family=Arimo:wght@400;700&family=Archivo+Black&display=swap">
<style>
  :root {
    --green: #5cb947;
    --green-dark: #3f9a32;
    --mint: #dcebd8;
    --grey: #8d8d93;
    --grey-dark: #6f6f75;
    --grey-light: #d9d9de;
    --grey-pale: #ececef;
    --ink: #333338;
    --white: #ffffff;
    --page: #eeeeee;
    --photo-warm: #c9b8a8;
    --photo-cool: #c7ccd3;
  }
  * { box-sizing: border-box; margin: 0; padding: 0; }
  html, body { width: 1200px; height: 800px; overflow: hidden; background: var(--page); }
  body { font-family: "Arimo", Arial, sans-serif; color: var(--ink); }

  .brochure {
    position: absolute; left: 75px; top: 30px;
    width: 1050px; height: 740px;
    display: flex;
    box-shadow: 0 6px 18px rgba(0,0,0,.15);
  }
  .panel { position: relative; width: 350px; height: 740px; overflow: hidden; }
  .panel-bg { position: absolute; inset: 0; width: 100%; height: 100%; }

  /* ---------- Program panel ---------- */
  .program { background: var(--grey-light); }
  .week-banner {
    position: absolute; left: 0; height: 44px; width: 230px;
    display: flex; align-items: center; padding-left: 32px;
    font-family: "Playfair Display", Georgia, serif; font-weight: 700;
    font-size: 22px; color: var(--white);
  }
  .week-banner--green { top: 70px; background: var(--green); }
  .week-banner--grey { top: 290px; background: var(--grey-dark); }
  .session {
    position: absolute; left: 30px; width: 295px;
    font-size: 14px; line-height: 1.35; font-weight: 700; color: var(--ink);
  }
  .session p + p { margin-top: 12px; }
  .session strong { font-weight: 700; text-decoration: underline; text-decoration-thickness: 1px; }
  .session--w5 { top: 126px; }
  .session--w6 { top: 350px; }
  .program-photo {
    position: absolute; left: 40px; top: 608px; width: 290px; height: 118px;
    border-radius: 6px;
    background: linear-gradient(135deg, #f2f2f4 0%, #d8d8dc 55%, var(--photo-cool) 100%);
  }

  /* ---------- Team panel ---------- */
  .team { background: var(--green); }
  .team-mark {
    position: absolute; left: 34px; top: 30px; width: 26px; height: 26px;
    background: var(--white);
  }
  .team-title {
    position: absolute; left: 90px; top: 28px;
    font-family: "Playfair Display", Georgia, serif; font-weight: 700;
    font-size: 22px; color: var(--white);
  }
  .team-list { position: absolute; left: 0; top: 66px; width: 350px; list-style: none; }
  .member {
    position: relative; height: 40px;
    display: flex; align-items: center;
  }
  .member-card {
    position: absolute; top: 4px; height: 32px; width: 250px;
    background: var(--white);
    clip-path: polygon(6% 0, 100% 0, 94% 100%, 0 100%);
    text-align: center; padding-top: 2px;
  }
  .member-card::after {
    content: ""; position: absolute; left: 0; right: 0; bottom: 0; height: 12px;
    background: var(--grey-dark);
  }
  .member--right .member-card { left: 40px; }
  .member--left .member-card { left: 62px; }
  .member-name {
    display: block; font-family: "Playfair Display", Georgia, serif; font-weight: 700;
    font-size: 12.5px; color: var(--ink); line-height: 17px;
  }
  .member-role {
    position: relative; z-index: 1; display: block;
    font-size: 7px; color: var(--white); text-transform: uppercase; line-height: 12px; letter-spacing: .2px;
  }
  .member-photo {
    position: absolute; top: 0; width: 40px; height: 40px; border-radius: 50%;
    border: 2px solid var(--white);
    background: radial-gradient(circle at 45% 40%, #e4cdb8, var(--photo-warm));
    z-index: 2;
  }
  .member--right .member-photo { right: 38px; }
  .member--left .member-photo { left: 22px; }

  .info { position: absolute; left: 30px; top: 528px; width: 300px; color: var(--white); }
  .info h3 {
    font-family: "Playfair Display", Georgia, serif; font-weight: 700;
    font-size: 14px; text-transform: uppercase; color: var(--white); margin-bottom: 3px;
  }
  .info p { font-size: 11.5px; line-height: 1.35; }
  .info h3 + p + h3 { margin-top: 10px; }
  .info .gap { margin-top: 8px; }

  /* ---------- Cover panel ---------- */
  .cover { background: var(--mint); }
  .brand {
    position: absolute; right: 44px; top: 30px;
    display: flex; align-items: center; gap: 10px;
  }
  .brand-square { width: 34px; height: 34px; background: var(--green); }
  .brand-name {
    font-family: "Playfair Display", Georgia, serif; font-weight: 700;
    font-size: 14px; line-height: 1.05; color: var(--grey-dark); text-transform: uppercase;
  }
  .cover-photo {
    position: absolute; left: 70px; top: 150px; width: 230px; height: 170px;
    background: var(--white); padding: 9px;
    transform: rotate(7deg);
    box-shadow: 0 3px 8px rgba(0,0,0,.25);
  }
  .cover-photo-fill {
    width: 100%; height: 100%;
    background: linear-gradient(120deg, #b9d6ea 0%, #e7cdb8 45%, var(--photo-warm) 100%);
  }
  .title-bar {
    position: absolute; left: 0; top: 408px; width: 350px; height: 40px;
    background: var(--white);
    display: flex; align-items: center; padding-left: 40px;
  }
  .title {
    font-family: "Archivo Black", "Arial Black", sans-serif;
    font-size: 29px; color: var(--green); text-transform: uppercase; letter-spacing: .5px;
  }
</style>
</head>
<body>
<main class="brochure">

  <!-- Program panel -->
  <section class="panel program">
    <svg class="panel-bg" viewBox="0 0 350 740" aria-hidden="true">
      <polygon points="0,0 350,0 350,44 150,44" fill="var(--grey-pale)"/>
      <polygon points="230,70 350,70 350,275 280,275" fill="var(--grey-pale)"/>
      <polygon points="230,70 270,70 230,114" fill="var(--grey-dark)"/>
      <polygon points="230,290 270,290 230,334" fill="var(--green)"/>
      <polygon points="0,334 0,372 36,334" fill="var(--green)"/>
    </svg>
    <div class="week-banner week-banner--green">Week 5</div>
    <div class="session session--w5">
      <p><strong>Session 1</strong> – Clinical Psychologist Dr Megan Ashby will share information about bonding &amp; attachment with your baby, how to promote their social &amp; emotional development and how to manage separation anxiety. She will also discuss positive parenting approaches.</p>
    </div>
    <div class="week-banner week-banner--grey">Week 6</div>
    <div class="session session--w6">
      <p><strong>Session 1</strong> – Secret Men's Business – a men-only session (including beer!) with a new father for frank discussion about the road ahead. Mums will do a shopping excursion with the GP &amp; Dietician to FreshMart to look at baby products and food – the good and the bad!</p>
      <p><strong>Session 2</strong> – Program review, reflection and evaluation and future session planning when baby is 6 months of age.</p>
    </div>
    <div class="program-photo" role="img" aria-label="Photo of a father holding his newborn baby"></div>
  </section>

  <!-- Team panel -->
  <section class="panel team">
    <svg class="panel-bg" viewBox="0 0 350 740" aria-hidden="true">
      <polygon points="0,0 180,0 0,24" fill="var(--grey-pale)"/>
      <polygon points="0,0 90,0 0,14" fill="var(--white)"/>
      <polygon points="0,380 350,300 350,540 0,540" fill="var(--green-dark)" opacity=".35"/>
    </svg>
    <div class="team-mark" aria-hidden="true"></div>
    <h2 class="team-title">The Team</h2>
    <ul class="team-list">
      <li class="member member--right"><div class="member-card"><span class="member-name">Dr Helena Marsh</span><span class="member-role">MBBS, FRACGP, DCH</span></div><div class="member-photo" role="img" aria-label="Portrait of Dr Helena Marsh"></div></li>
      <li class="member member--left"><div class="member-photo" role="img" aria-label="Portrait of Dr Oliver Grant"></div><div class="member-card"><span class="member-name">Dr Oliver Grant</span><span class="member-role">MBBS, FRACGP, B.Sc</span></div></li>
      <li class="member member--right"><div class="member-card"><span class="member-name">Dr Maeve Doyle</span><span class="member-role">MB BCh BAO, FRACGP</span></div><div class="member-photo" role="img" aria-label="Portrait of Dr Maeve Doyle"></div></li>
      <li class="member member--left"><div class="member-photo" role="img" aria-label="Portrait of Dr Sienna Ward"></div><div class="member-card"><span class="member-name">Dr Sienna Ward</span><span class="member-role">MBBS</span></div></li>
      <li class="member member--right"><div class="member-card"><span class="member-name">Tessa Whitfield</span><span class="member-role">Bachelor of Podiatry &amp; Nursing</span></div><div class="member-photo" role="img" aria-label="Portrait of Tessa Whitfield"></div></li>
      <li class="member member--left"><div class="member-photo" role="img" aria-label="Portrait of Dr Clara Voss"></div><div class="member-card"><span class="member-name">Dr Clara Voss</span><span class="member-role">MBBS</span></div></li>
      <li class="member member--right"><div class="member-card"><span class="member-name">Liam Prescott</span><span class="member-role">B. Physiotherapy, B. Exercise Science</span></div><div class="member-photo" role="img" aria-label="Portrait of Liam Prescott"></div></li>
      <li class="member member--left"><div class="member-photo" role="img" aria-label="Portrait of Isla Brennan"></div><div class="member-card"><span class="member-name">Isla Brennan</span><span class="member-role">BA of Exsc, Doctorate of Physiotherapy</span></div></li>
      <li class="member member--right"><div class="member-card"><span class="member-name">Amy Calder</span><span class="member-role">Nutritionist</span></div><div class="member-photo" role="img" aria-label="Portrait of Amy Calder"></div></li>
      <li class="member member--left"><div class="member-photo" role="img" aria-label="Portrait of Ruth Ellison"></div><div class="member-card"><span class="member-name">Ruth Ellison</span><span class="member-role">Paediatric Speech Pathologist</span></div></li>
      <li class="member member--right"><div class="member-card"><span class="member-name">Nina Holt</span><span class="member-role">B. Exsc, Grad Dip Clinical Ex Phys</span></div><div class="member-photo" role="img" aria-label="Portrait of Nina Holt"></div></li>
    </ul>
    <div class="info">
      <h3>Opening Hours</h3>
      <p>Monday to Friday: 8:30am – 5:00pm<br>Saturday: 8:00am – 12:00pm<br>Sunday &amp; Public Holidays: Closed</p>
      <h3>Contact Information</h3>
      <p>Wattlebrook Shopping Village, Shop 4<br>120 Banksia Way, Wattlebrook NSW 2000</p>
      <p class="gap">Phone: 02 5550 0142 &nbsp;•&nbsp; Fax: 02 5550 0143<br>Email: hello@wattlebrookhealth.com.au</p>
    </div>
  </section>

  <!-- Cover panel -->
  <section class="panel cover">
    <svg class="panel-bg" viewBox="0 0 350 740" aria-hidden="true">
      <rect x="0" y="0" width="350" height="740" fill="var(--mint)"/>
      <polygon points="0,0 220,0 0,120" fill="var(--grey-pale)"/>
      <polygon points="130,0 350,0 350,110" fill="var(--white)"/>
      <polygon points="40,40 150,40 150,150 40,150" fill="var(--grey)"/>
      <polygon points="150,130 350,110 350,470 160,470" fill="var(--green)"/>
      <polygon points="0,250 130,470 0,470" fill="#c8dfc3"/>
      <polygon points="60,448 250,448 230,560 90,600" fill="var(--green)"/>
      <polygon points="0,470 60,448 0,600" fill="var(--grey-pale)"/>
      <polygon points="250,448 350,448 350,740 180,740" fill="var(--grey)"/>
      <polygon points="0,600 180,740 0,740" fill="#c8dfc3"/>
    </svg>
    <div class="brand">
      <div class="brand-square" aria-hidden="true"></div>
      <div class="brand-name">Wattlebrook<br>Health &amp;<br>Medical</div>
    </div>
    <div class="cover-photo">
      <div class="cover-photo-fill" role="img" aria-label="Photo of smiling parents holding their baby"></div>
    </div>
    <div class="title-bar"><h1 class="title">Little Lantern</h1></div>
  </section>

</main>
</body>
</html>
```